Website for Excavator and Earthworks Company

We require a modern, sleek and practical website for our newly created earthworks/excavator business in Perth, Western Australia called Bluegum Ridge Earthworks.

The website should have a modern, cutting edge feel but only needs to be relatively simplistic in it's layout and eventual functionality.

Some pages it should have would be Home, About, Projects and Contact Us.

```html
<!DOCTYPE html>
<html lang="en">
<head>
<meta charset="utf-8">
<title>Bluegum Ridge Earthworks</title>
<link href="https://fonts.googleapis.com/css2?family=Exo+2:wght@600;700;800&family=Roboto:wght@400;500;700&display=swap" rel="stylesheet">
<style>
:root{
  --lime:#c9d400;
  --lime-dark:#a9b300;
  --black:#111111;
  --ink:#1c1c1c;
  --grey:#2c2c2c;
  --mid:#5a5a5a;
  --light:#f2f2ee;
  --white:#ffffff;
}
*{box-sizing:border-box;margin:0;padding:0}
html,body{width:1200px;height:4496px;overflow:hidden}
body{position:relative;background:var(--white);font-family:"Roboto",Arial,sans-serif;color:var(--ink)}
.abs{position:absolute}
h1,h2,h3,.brand-name,.btn{font-family:"Exo 2","Roboto",sans-serif}

/* header */
.site-header{position:absolute;left:0;top:0;width:1200px;height:150px;background:var(--white);z-index:5}
.brand{position:absolute;left:110px;top:34px;display:flex;align-items:center;gap:12px}
.brand-mark{width:34px;height:34px;background:var(--lime)}
.brand-name{font-weight:800;font-size:27px;line-height:1.05;color:var(--black);text-transform:uppercase;width:200px}
.topbar{position:absolute;left:470px;top:10px;height:34px;width:600px;display:flex;align-items:center;gap:28px;font-size:13px;color:var(--ink)}
.topbar span{display:flex;align-items:center;gap:8px}
.dot-ic{width:18px;height:18px;border-radius:50%;background:var(--lime);display:inline-block}
.social{display:flex;gap:8px;margin-left:auto}
.social i{width:20px;height:20px;border-radius:50%;background:var(--black);display:block}
.nav{position:absolute;left:530px;top:82px;display:flex;gap:26px;align-items:center;font-size:14px;font-weight:500;text-transform:uppercase}
.nav .active{border-bottom:2px solid var(--lime);padding-bottom:4px}
.btn{display:inline-block;background:var(--lime);color:var(--black);font-weight:700;font-size:14px;text-transform:uppercase;padding:10px 20px;clip-path:polygon(0 0,100% 0,92% 100%,0 100%)}
.btn.dark{background:var(--black);color:var(--white)}
.nav .btn{margin-left:10px}

/* hero */
.hero-photo{left:0;top:140px;width:1200px;height:720px;background:linear-gradient(160deg,#8fa6b8 0%,#c8c2b4 35%,#8c7350 60%,#4c3a28 100%);clip-path:polygon(0 0,100% 0,100% 90%,0 100%)}
.hero-shade{left:470px;top:140px;width:730px;height:720px;background:linear-gradient(90deg,rgba(0,0,0,0) 0%,rgba(0,0,0,.65) 25%,rgba(0,0,0,.75) 100%);clip-path:polygon(0 0,100% 0,100% 90%,0 100%)}
.hero-band{left:0;top:790px;width:1200px;height:100px;background:var(--lime);clip-path:polygon(0 88%,100% 0,100% 30%,0 100%)}
.hero-title{left:535px;top:300px;width:620px;font-weight:800;font-size:46px;line-height:1.15;color:var(--white);text-transform:uppercase}
.hero-title em{font-style:normal;color:var(--lime)}
.hero-sub{left:535px;top:490px;width:470px;font-size:19px;font-weight:500;color:var(--white);line-height:1.4}
.hero-btns{left:535px;top:595px;display:flex;gap:24px}
.dots{left:1010px;top:800px;display:flex;gap:8px}
.dots i{width:9px;height:9px;border-radius:50%;background:var(--white);display:block}

/* services */
.section-title{width:1200px;text-align:center;font-weight:800;font-size:50px;text-transform:uppercase;color:var(--black)}
.section-title em{font-style:normal;color:var(--lime)}
.hex{width:264px;height:300px;clip-path:polygon(50% 0,100% 25%,100% 75%,50% 100%,0 75%,0 25%);background:var(--black);color:var(--white);text-align:center;padding:70px 32px 0}
.hex.lime{background:var(--lime);color:var(--black)}
.hex-ring{width:262px;height:302px;clip-path:polygon(50% 0,100% 25%,100% 75%,50% 100%,0 75%,0 25%);background:var(--black)}
.hex h3{font-size:19px;font-weight:700;line-height:1.2;margin-bottom:10px}
.hex p{font-size:11px;line-height:1.45}
.hex-icon{position:absolute;left:50%;top:22px;transform:translateX(-50%);width:36px;height:36px;border:3px solid currentColor;border-radius:6px}
.hex-arrow{position:absolute;left:50%;bottom:52px;transform:translateX(-50%);width:26px;height:26px;border-radius:50%;border:2px solid currentColor;display:flex;align-items:center;justify-content:center;font-size:12px}
.machines-photo{left:0;top:1560px;width:1200px;height:260px;background:linear-gradient(180deg,#ffffff 0%,#e8e6dc 40%,#bdb9a4 100%);opacity:.9}
.machines-band{left:0;top:1700px;width:1200px;height:200px;background:var(--lime);clip-path:polygon(0 70%,100% 0,100% 100%,0 100%)}

/* about */
.about{left:0;top:1890px;width:1200px;height:520px;background:linear-gradient(180deg,#ffffff 0%,var(--light) 100%)}
.about h2{left:145px;top:1880px;font-weight:800;font-size:54px;text-transform:uppercase;color:var(--black)}
.about-text{left:145px;top:1965px;width:560px;font-size:15.5px;line-height:1.75;color:var(--mid);text-align:justify}
.about-btn{left:145px;top:2270px}
.about-deco{left:770px;top:1960px;width:280px;height:280px;background:rgba(201,212,0,.35)}

/* gallery */
.gallery-title{top:2490px}
.tile{width:262px;height:250px;clip-path:polygon(8% 0,100% 0,92% 100%,0 100%)}
.g1{background:linear-gradient(135deg,#e9b26b,#8a5a2e)}
.g2{background:linear-gradient(135deg,#c9a27a,#7e5a3c)}
.g3{background:linear-gradient(135deg,#5a4632,#2a2018)}
.g4{background:linear-gradient(135deg,#d98a3b,#5b3b20)}
.g5{background:linear-gradient(135deg,#9bb7d1,#5f6a4a)}
.g6{background:linear-gradient(135deg,#7fb2e0,#4d7a3a)}
.g7{background:linear-gradient(135deg,#a8c6e2,#a78760)}
.g8{background:linear-gradient(135deg,#d7e6f2,#6f7f90)}
.zoom{left:694px;top:2737px;width:36px;height:36px;border-radius:50%;background:var(--lime);color:var(--black);font-weight:700;font-size:24px;text-align:center;line-height:34px}
.gallery-btn{left:480px;top:3220px}

/* contact */
.contact-bg{left:0;top:3150px;width:1200px;height:820px;background:linear-gradient(180deg,rgba(255,255,255,0) 0%,#9aa5b0 12%,#5a5f66 24%,#333 40%,var(--grey) 100%)}
.contact-photo{left:150px;top:3460px;width:370px;height:420px;background:linear-gradient(160deg,#9fa2a4 0%,#6e6a5c 55%,#c7b84a 80%,#3a3a3a 100%);clip-path:polygon(12% 0,100% 0,100% 100%,0 100%)}
.contact-title{left:585px;top:3520px;font-weight:800;font-size:54px;color:var(--white);text-transform:uppercase}
.contact-title em{font-style:normal;color:var(--lime)}
.field{background:var(--white);height:40px;width:218px;font-size:14px;padding:11px 14px;color:var(--ink)}
.field.wide{width:446px;height:86px}
.submit{left:590px;top:3862px}

/* footer */
.footer-brand{left:220px;top:4180px}
.footer-brand .brand-name{width:230px}
.links{left:520px;top:4185px}
.col-title{font-family:"Exo 2",sans-serif;font-weight:700;font-size:18px;text-transform:uppercase;color:var(--black);border-left:3px solid var(--lime);padding-left:8px;margin-bottom:12px}
.links ul{list-style:none;font-size:14px;line-height:1.75;padding-left:11px}
.newsletter{left:725px;top:4185px;width:360px}
.news-field{border:1px solid #bbb;height:38px;width:270px;font-size:13px;padding:10px 12px;color:#555;margin-bottom:10px}
.foot-bar{left:0;top:4390px;width:1200px;height:106px;border-top:1px solid #ddd}
.copy{left:145px;top:4415px;font-size:13px;color:var(--mid)}
.foot-social{left:965px;top:4428px;display:flex;gap:10px}
.foot-social i{width:24px;height:24px;border-radius:50%;background:var(--black);display:block}
.foot-social i.on{background:var(--lime)}
</style>
</head>
<body>

<header class="site-header">
  <div class="brand"><span class="brand-mark"></span><span class="brand-name">Bluegum Ridge Earthworks</span></div>
  <div class="topbar">
    <span><i class="dot-ic"></i>Call Us : +61 8 5550 1234</span>
    <span><i class="dot-ic"></i>hello@bluegumridge.example</span>
    <div class="social"><i></i><i></i><i></i></div>
  </div>
  <nav class="nav">
    <a class="active">Home</a><a>About</a><a>Projects</a><a>Contact Us</a>
    <a class="btn">Get a Quote</a>
  </nav>
</header>

<section class="hero">
  <div class="abs hero-photo" role="img" aria-label="Bulldozer working on an earthworks site under a blue sky"></div>
  <div class="abs hero-shade"></div>
  <div class="abs hero-band"></div>
  <h1 class="abs hero-title">Professional<br><em>Earthmoving &amp;</em><br>Excavation in Perth</h1>
  <p class="abs hero-sub">Reliable, modern earthworks solutions delivered with precision and efficiency.</p>
  <div class="abs hero-btns"><a class="btn">Get a Quote</a><a class="btn dark">View Projects</a></div>
  <div class="abs dots"><i></i><i></i><i></i><i></i></div>
</section>

<section class="services">
  <h2 class="abs section-title" style="left:0;top:940px">What <em>We Do</em></h2>

  <div class="abs hex" style="left:148px;top:1080px"><span class="hex-icon"></span><h3>Excavation &amp;<br>Earthmoving</h3><p>Precise digs for footings, pools and basements across Perth metro sites.</p><span class="hex-arrow">&#10095;</span></div>
  <div class="abs hex-ring" style="left:467px;top:1059px"></div>
  <div class="abs hex lime" style="left:468px;top:1060px"><span class="hex-icon"></span><h3>Site Preparation</h3><p>Clearing, levelling and compaction so your build starts on solid ground.</p><span class="hex-arrow">&#10095;</span></div>
  <div class="abs hex" style="left:788px;top:1080px"><span class="hex-icon"></span><h3>Trenching &amp;<br>Foundations</h3><p>Clean trenches for services, drainage and strip footings done right.</p><span class="hex-arrow">&#10095;</span></div>
  <div class="abs hex lime" style="left:308px;top:1300px"><span class="hex-icon"></span><h3>Land Clearing</h3><p>Vegetation and debris removal with careful disposal and tidy finishes.</p><span class="hex-arrow">&#10095;</span></div>
  <div class="abs hex lime" style="left:628px;top:1300px"><span class="hex-icon"></span><h3>Residential &amp;<br>Commercial Works</h3><p>Bulk earthworks for shops, estates and new home developments.</p><span class="hex-arrow">&#10095;</span></div>

  <div class="abs machines-photo" role="img" aria-label="Faded view of yellow excavators and trucks on site" style="z-index:-1"></div>
  <div class="abs machines-band"></div>
</section>

<section>
  <div class="abs about"></div>
  <div class="about">
    <h2 class="abs" style="left:145px;top:1880px;font-weight:800;font-size:54px;text-transform:uppercase;color:var(--black)">About Us</h2>
  </div>
  <p class="abs about-text">Sed ut perspiciatis unde omnis iste natus error sit voluptatem accusantium doloremque laudantium, totam rem aperiam, eaque ipsa quae ab illo inventore veritatis et quasi architecto beatae vitae dicta sunt explicabo. Nemo enim ipsam voluptatem quia voluptas sit aspernatur aut odit aut fugit, sed quia consequuntur magni dolores eos qui ratione voluptatem sequi nesciunt. Neque porro quisquam est, qui dolorem ipsum quia dolor sit amet, consectetur.</p>
  <a class="abs btn dark about-btn">Read More</a>
  <div class="abs about-deco"></div>
</section>

<section class="gallery">
  <h2 class="abs section-title gallery-title" style="left:0">Project <em>Gallery</em></h2>
  <div class="abs tile g1" style="left:100px;top:2625px" role="img" aria-label="Excavator digging at sunset"></div>
  <div class="abs tile g2" style="left:350px;top:2625px" role="img" aria-label="Brick foundations under construction"></div>
  <div class="abs tile g3" style="left:600px;top:2625px" role="img" aria-label="Close view of an excavator bucket in soil"></div>
  <div class="abs tile g4" style="left:850px;top:2625px" role="img" aria-label="Bulldozer pushing dirt at dusk"></div>
  <div class="abs tile g5" style="left:85px;top:2895px" role="img" aria-label="Workers in hard hats on a site"></div>
  <div class="abs tile g6" style="left:335px;top:2895px" role="img" aria-label="Yellow machinery beside green trees"></div>
  <div class="abs tile g7" style="left:585px;top:2895px" role="img" aria-label="Bulldozer on a cleared lot"></div>
  <div class="abs tile g8" style="left:835px;top:2895px" role="img" aria-label="Worker on a steel frame structure"></div>
  <div class="abs zoom">+</div>
  <a class="abs btn gallery-btn">View More Projects</a>
</section>

<section class="contact">
  <div class="abs contact-bg" role="img" aria-label="Mountain range fading into a dark backdrop" style="z-index:-1"></div>
  <div class="abs contact-photo" role="img" aria-label="Yellow bulldozer on a dark background"></div>
  <h2 class="abs contact-title">Contact <em>Us</em></h2>
  <div class="abs field" style="left:590px;top:3625px">Enter Name</div>
  <div class="abs field" style="left:818px;top:3625px">Enter Email</div>
  <div class="abs field" style="left:590px;top:3683px">Enter Phone</div>
  <div class="abs field" style="left:818px;top:3683px">Address</div>
  <div class="abs field wide" style="left:590px;top:3741px">Message</div>
  <a class="abs btn submit">Submit Message</a>
</section>

<footer>
  <div class="abs brand footer-brand" style="position:absolute"><span class="brand-mark"></span><span class="brand-name">Bluegum Ridge Earthworks</span></div>
  <div class="abs links">
    <div class="col-title">Links</div>
    <ul><li>Home</li><li>About</li><li>Projects</li><li>Contact Us</li></ul>
  </div>
  <div class="abs newsletter">
    <div class="col-title">Subscribe to our Newsletter</div>
    <div class="news-field">Enter Email</div>
    <a class="btn">Subscribe</a>
  </div>
  <div class="abs foot-bar"></div>
  <p class="abs copy">© 2026 Bluegum Ridge All Rights Reserved &nbsp;|&nbsp; Privacy Policy &nbsp;|&nbsp; Terms of Use</p>
  <div class="abs foot-social"><i></i><i class="on"></i><i></i></div>
</footer>

</body>
</html>
```